Visualisation Software brochure

i need a sales brochure for a new visualisation software company called Lumora Studio Max.
The software has been specifically designed for manufacturers, distributers and retailers in the design / décor / furnishing / building industries. It allows customers can then import unlimited numbers of digital photos of rooms from their own home or take advantage of a library of pre-made photos, and then render different products from your catalogue into that photo to see what the finished look will be.
i have attached:
1) a mock up of the home page of the website
2) example of brochure wording that i have put together (although i am a little unsure about what other words i can add - so any suggestions here would be good)
3) i have attached some examples of other brochures that i like and would like similar designs
I am after a classy brochure used by a large corporate technology company that is given to executives and gives an impression of quality, trustworthiness and innovation.
• the colour blue as per the colours on my website mock up provided in the design brief
• I like simple, smart, clean and uncluttered design
• I like simple, clean and uncluttered design
• I like pictures that fit in with my technology (whether that be home and interior design, mixing virtual world and real world, visualising an idea) rather than basic stock of corporate people
Updates
Target Market(s)
marketing professionals
Industry/Entity Type
Software
Font styles to use
Look and feel
Each slider illustrates characteristics of the customer's brand and the style your logo design should communicate.

```html
<!DOCTYPE html>
<html lang="en">
<head>
<meta charset="utf-8">
<title>Lumora Studio Max – Brochure Page</title>
<link href="https://fonts.googleapis.com/css2?family=Roboto+Condensed:wght@300;400&display=swap" rel="stylesheet">
<style>
  :root {
    --teal: #17a398;
    --ink: #3a3a3a;
    --heading: #2e2e2e;
    --paper-top: #ffffff;
    --paper-bottom: #ececec;
    --hero-light: #eef0f1;
    --hero-mid: #d9dadb;
    --hero-warm: #a88466;
  }
  * { margin: 0; padding: 0; box-sizing: border-box; }
  html, body { width: 848px; height: 1200px; overflow: hidden; }
  body {
    background: linear-gradient(180deg, var(--paper-top) 465px, #f7f7f7 700px, var(--paper-bottom) 1200px);
    font-family: "Roboto Condensed", "Arial Narrow", sans-serif;
    color: var(--ink);
  }
  .page { position: relative; width: 848px; height: 1200px; }
  .top-band { height: 60px; background: var(--teal); }
  .hero {
    height: 405px;
    background:
      radial-gradient(ellipse 260px 200px at 540px 230px, rgba(168,132,102,0.55), rgba(168,132,102,0) 100%),
      radial-gradient(ellipse 120px 50px at 90px 400px, rgba(190,140,90,0.5), rgba(190,140,90,0) 100%),
      linear-gradient(160deg, var(--hero-light) 0%, var(--hero-mid) 100%);
  }
  .columns {
    position: absolute;
    top: 524px;
    left: 38px;
    right: 38px;
    display: flex;
    justify-content: space-between;
  }
  .column { width: 368px; }
  .column h2 {
    font-weight: 400;
    font-size: 19.5px;
    line-height: 24px;
    color: var(--heading);
    margin-bottom: 12px;
  }
  .column--solution h2 { margin-top: 0; margin-bottom: 18px; }
  .column p {
    font-weight: 300;
    font-size: 12.6px;
    line-height: 16px;
    text-align: justify;
    hyphens: auto;
    margin-bottom: 16px;
  }
  .column p.tight { margin-bottom: 0; }
</style>
</head>
<body>
<div class="page">
  <div class="top-band"></div>
  <div class="hero" role="img" aria-label="Miniature model house with brick walls and a balcony resting on architectural plans, beside pencils and an eraser"></div>

  <div class="columns">
    <section class="column column--challenge">
      <h2>The Challenge for Both Customers<br>and Retailers</h2>
      <p>Gone are the days when all you needed was a showroom, a product line, and a business card. Customers are better informed, more interactive, and more selective than ever before. With access to a range of new technologies and a wide variety of online resources, these connected consumers are increasingly demanding a dynamic, seamless, integrated, consistent, accessible and personalised experience with your brand across all online, bricks-and-mortar and mobile channels.</p>
      <p>The customer must be empowered to interact across all touchpoints and channels; they want to browse and buy on their own schedules and retailers must offer equally accurate and immediate access to products and customer service. Consumers want to be inspired and be given the tools, advice and confidence to create unique, personal spaces - meaning companies need to feed this design dream and appealing to their vision is essential. The shopping experience should be built around the new reality that most consumers make their browsing and purchasing commitments online, often before they ever see the product in person.</p>
      <p>Amid ongoing economic uncertainty, true omni-channel retailers need to continue to focus on understanding the customer psyche and leveraging innovation to drive loyalty and customer engagement and ultimately increase sales.</p>
    </section>

    <section class="column column--solution">
      <h2>The Virtualised Solution</h2>
      <p>Having your own branded virtual design software embedded on your website or accessible via an Orbis and/or Quillon app will help bridge the gap between your customers’ design dreams and your products. Our software helps solve one of the biggest problems many experience whilst redecorating or designing their home, which is despite looking at numerous samples, most cannot visualise or conceptualise what the finished look will be.</p>
      <p class="tight">It doesn’t matter what business you’re in. Your customers will be able to visualise all possible product combinations for their new home – it just depends on your range. The software can easily handle ‘flat surface products’ including roofing, cladding, garage doors, windows and driveways/pathways to interior products such as carpet, tiles, timber and laminate flooring, doors, art works, bench tops and splash-backs.</p>
      <p>Importantly, our technology can also handle any product in 3D - whether it be furniture, lighting, floor rugs, curtains / blinds, wardrobes, household items, kitchen cabinets and bathroom fixtures. A truly unique feature allows customers to simply delete the existing item from their photo and replace it with another product from your catalogue without removing any item physically.</p>
      <p>Today’s consumer doesn’t just rely on technological gimmicks such as augmented reality or one in-store visit before making important investment decisions. With so much competition in the marketplace consumers are more driven than ever to shop around with the amount and quality of value-adding service the real deal breaker rather than price.</p>
      <p>It has become more about initiating the education of your customer versus waiting for them to ask for assistance. Using our technology can increase sales conversion rates as once customers have identified what products they would like to purchase they come to you as educated buyers, already having experienced a fantastic customer interaction with your brand.</p>
    </section>
  </div>
</div>
</body>
</html>
```